Pawn & Gun store business card design

Hello! We would like a new business card design for our pawn & gun store. We loan money on items of value and sell firearms, jewelry, electronics & more.

Card will need to have the following information:

Business name - Prairie Nickel Pawn & Gun
Address - 2417 Hwy 53 S. Suite C Wylie, TX 75246
Employees name - Darren Kellum
Phone number - 972-613-8840
Email - PrairieNickelPawn@Mailvera.com
Website - PrairieNickelPawn.com

Somewhere on the card we would like it to say "Offering 10 Month Layaway!" & "We buy & loan on anything of value!". Our main store color is orange (please see logo). Logo does not have to be on the business card but it can be. Would like the back to have an area to write a note on the back. We like vintage things like old coins, collectables, firearms and more so think about this in the design. We want a business card as unique as our store!

Colors

Designer to choose colors to be used in the design.

Requirements
Nice to have
• Vintage Style

```html
<!DOCTYPE html>
<html lang="en">
<head>
<meta charset="utf-8">
<title>Prairie Nickel Pawn &amp; Gun – Business Card</title>
<link rel="stylesheet" href="https://fonts.googleapis.com/css2?family=Cabin:wght@700&family=Questrial&display=swap">
<style>
  :root {
    --stage: #646464;
    --card: #ffffff;
    --orange: #d9601f;
    --brown: #3a1a0a;
    --ink: #3b3b3b;
    --dash: #555555;
    --copper: #9a5a3c;
    --silver: #b9b9b9;
    --steel: #a8a8a8;
    --gunmetal: #3c3c3c;
  }
  * { box-sizing: border-box; margin: 0; padding: 0; }
  html, body { width: 1125px; height: 1200px; overflow: hidden; }
  body { background: var(--stage); position: relative; font-family: "Questrial", sans-serif; color: var(--ink); }

  .card {
    position: absolute; left: 178px; width: 768px; height: 436px;
    background: var(--card); border-radius: 24px; overflow: hidden;
    box-shadow: 0 4px 10px rgba(0,0,0,.35);
  }
  .card--front { top: 140px; }
  .card--back { top: 626px; }

  /* Front */
  .holder-name {
    position: absolute; right: 422px; top: 196px;
    font-family: "Cabin", sans-serif; font-weight: 700; font-size: 31px; white-space: nowrap;
  }
  .holder-name .first { color: var(--orange); }
  .holder-name .last { color: var(--brown); }
  .divider { position: absolute; left: 384px; top: 154px; width: 2px; height: 126px; background: var(--orange); }
  .contact { position: absolute; left: 428px; top: 148px; font-size: 17.5px; line-height: 22px; }
  .address { margin-bottom: 13px; }
  .contact-row { display: flex; align-items: center; height: 29px; white-space: nowrap; }
  .contact-row svg { width: 14px; height: 14px; margin-right: 9px; flex: none; }
  .contact-row .accent { color: var(--orange); }

  .promo-band {
    position: absolute; left: 0; right: 0; top: 376px; height: 43px;
    background: var(--orange); color: #fff; font-size: 18.5px;
    display: flex; align-items: center; justify-content: center;
    border-top: 2px solid var(--brown); border-bottom: 2px solid var(--brown);
    box-shadow: inset 0 2px 0 #fff, inset 0 -2px 0 #fff;
  }

  /* Back */
  .wares { position: absolute; top: 50px; left: 0; right: 0; height: 110px; }
  .ware { position: absolute; top: 0; width: 110px; margin-left: -55px; height: 110px; display: flex; flex-direction: column; align-items: center; }
  .ware-photo { height: 78px; display: flex; align-items: center; justify-content: center; }
  .ware-label {
    margin-top: 10px; background: var(--orange); color: #fff; font-size: 16px;
    padding: 0 4px; line-height: 19px; white-space: nowrap;
  }
  .photo-coin { width: 75px; height: 75px; border-radius: 50%; background: var(--copper); }
  .photo-silver { width: 92px; height: 60px; border-radius: 8px; background: linear-gradient(#d0d0d0, var(--silver)); }
  .photo-ring { width: 70px; height: 62px; border-radius: 40%; background: var(--steel); }
  .photo-clock { width: 56px; height: 78px; border-radius: 28px; background: linear-gradient(#c9c9c9, var(--steel)); }
  .photo-firearm { width: 82px; height: 56px; border-radius: 4px; background: var(--gunmetal); }

  .notes-title {
    position: absolute; top: 204px; left: 0; right: 0; text-align: center;
    font-family: "Cabin", sans-serif; font-weight: 700; font-size: 21px; color: var(--orange);
  }
  .note-line { position: absolute; left: 58px; width: 675px; border-top: 1px dashed var(--dash); }
</style>
</head>
<body>

<section class="card card--front" aria-label="Card front">
  <h1 class="holder-name"><span class="first">Darren</span> <span class="last">Kellum</span></h1>
  <div class="divider"></div>
  <div class="contact">
    <p class="address">2417 Hwy 53 S. Suite<br>C Wylie, TX 75246</p>
    <p class="contact-row">
      <svg viewBox="0 0 16 16" aria-hidden="true"><path fill="#d9601f" d="M3 1.5l3 3-1.6 1.8c.9 1.9 2.4 3.4 4.3 4.3L10.5 9l3 3-1.8 2.3C6.4 14 2 9.6 1.7 3.3z"/></svg>
      972-613-8840
    </p>
    <p class="contact-row">
      <svg viewBox="0 0 16 16" aria-hidden="true"><rect x="1" y="3" width="14" height="10" fill="#d9601f"/><path d="M3 5l5 4 5-4" stroke="#fff" stroke-width="1.6" fill="none"/></svg>
      PrairieNickelPawn@Mailvera.com
    </p>
    <p class="contact-row">
      <svg viewBox="0 0 16 16" aria-hidden="true"><circle cx="8" cy="8" r="7" fill="#d9601f"/><path d="M4 4c2 1 1 3 3 3s1 3 0 5M10 2c0 2 2 2 3 4" stroke="#fff" stroke-width="1.4" fill="none"/></svg>
      <span>www.<span class="accent">PrairieNickelPawn</span>.com</span>
    </p>
  </div>
  <div class="promo-band">Offering 10 Month Layaway!" &amp; "We buy &amp; loan on anything of value!</div>
</section>

<section class="card card--back" aria-label="Card back">
  <div class="wares">
    <div class="ware" style="left:97px">
      <div class="ware-photo"><div class="photo-coin" role="img" aria-label="Photo of an old copper coin"></div></div>
      <span class="ware-label">Old Coins</span>
    </div>
    <div class="ware" style="left:251px">
      <div class="ware-photo"><div class="photo-silver" role="img" aria-label="Photo of a silver tea service on a tray"></div></div>
      <span class="ware-label">Collectables</span>
    </div>
    <div class="ware" style="left:396px">
      <div class="ware-photo"><div class="photo-ring" role="img" aria-label="Photo of a diamond ring"></div></div>
      <span class="ware-label">Jewelry</span>
    </div>
    <div class="ware" style="left:536px">
      <div class="ware-photo"><div class="photo-clock" role="img" aria-label="Photo of a twin-bell alarm clock"></div></div>
      <span class="ware-label">Clock</span>
    </div>
    <div class="ware" style="left:677px">
      <div class="ware-photo"><div class="photo-firearm" role="img" aria-label="Photo of a handgun"></div></div>
      <span class="ware-label">Firearms</span>
    </div>
  </div>
  <h2 class="notes-title">NOTES</h2>
  <div class="note-line" style="top:250px"></div>
  <div class="note-line" style="top:302px"></div>
  <div class="note-line" style="top:353px"></div>
  <div class="note-line" style="top:404px"></div>
</section>

</body>
</html>
```